Calder Aviation website

We are an aviation company based in Miramar, FL but with worldwide coverage. We are involved in commercial aircraft (mostly freighters) trading, sale & leasing. Specifically, we specialized in freighters of the Veltram family (V316, V328, V335, V342, V359). We also assist with financing, sale/leaseback. Handle special aviation projects and provide consultancy services. Currently engaged in a Veltram 359 passenger to Freighter conversion (P2F).

Website Preliminary Initial Content/Sections as follows:

About Us
Founded in 2011, Calder Aviation's management has many years of experience in Aviation, a strong background in scheduled airlines with emphasis in all cargo operations, freight forwarding supply chain and freight logistics, as well as ACMI and CMI operations.

Calder’s focuses in facilitating wet and dry lease operations, charter and ACMI programs consultancy, aircraft sales, leasing and procurement, aviation consultancy and aircraft management.

Calder team is a hands-on reliable alternative that works toward achieving your aircraft and aviation objectives by meeting your requirements and timeframe throughout professional and personalized service.

Tiberio Salcedo has over three decades of experience in the aviation field including aircraft maintenance, airline management, supply chain and logistics management. Tiberio is a true entrepreneur with proven experience and expertise on the multiple facets of the commercial aviation industry throughout the creation and development of a cluster of aviation entities. Tiberio is the founder and former sole member/chairman of 64 Air, a Veltram 342 All-Cargo U.S. Certificated Air Carrier created from scratch in 2014 which nowadays conforms a superb growing airline platform with an immaculate compliance operational record.

Services

Aircraft Finance, Trading, Procurement and Leasing
Calder buys, sells, leases and facilitates aircraft trading while specializes in structured aircraft investment projects. Calder has deep industry relationships and years of expertise, allowing to successfully execute lease transactions. We assist airlines, financial institutions and leasing companies when selling or purchasing aircraft.

Aircraft Available for Sale/Lease

Sale/Leaseback
Sale-leaseback is a method of financing. If your company needs liquidity, your aircraft or engine can serve as collateral for a loan throughout a sale-leaseback transaction. Sale-leaseback can free the equity tied up in aircraft or asset. Even if there is no pressing need for funds, a sale-leaseback allows you to use the equity tied up in your aircraft in a more productive fashion. Leaseback arrangements are usually employed because they confer financing, accounting or taxation benefits.

Passenger to Freighter Conversion (P2F)
Pandemic has seen the resurgence of operators packing freight into the main cabins of passenger aircraft. Carriers have been allowed to transport cargo in the cabin by removing passenger seats completely. NAB/CARO have established exemptions that allow operators to fly in “Preighter” configuration for a limited time. Calder is closely working with a U.S. group that is developing a Class E Supplemental Type Certificate (STC) for applicability on V359 aircraft which will include a cargo door for containerized freight. Final approvals are expected during first quarter of 2022.
Wet lease
Throughout our deep relationships within the industry, Calder facilitates short or long-term wet leases to airlines and qualified parties around the globe, whereby we provide the Aircraft, Crews, Maintenance and Insurance (ACMI) worldwide services at competitive rates. We also specialize in AM leases where the aircraft is registered onto Lessee´s AOC with all maintenance services included in the rates, covering all maintenance risks, or CM or CMI where the client provides the aircraft.

Dry Lease
We offer aircraft from our own portfolio on dry lease or could engage in procuring the aircraft of your choice.

Asset & Aircraft Management
We provide aircraft owners Aircraft Management services, where we manage the technical side of the aircraft or the asset. Calder also provides Harlow Dynamics engines trading, repair and full management services. We also buy Veltram/Skylane surplus inventory.

Worldwide Charters
We facilitate the arrangement of full charters to airlines and logistics companies. Certain territory restrictions may apply.

Aviation Consultancy
We provide airline consultancy services for new or special projects. Calder also specializes on All Cargo International route analysis, implementation and development. Our team provides professional guidance in obtaining worldwide both scheduled and charter authority.

Target Market(s)

Our target market are the airlines, logistics companies and commercial aviation related entities

Industry/Entity Type

Commercial Aviation

Coding

Coded - Design and coding required

Number of Pages Required

3 page

Requirements
Must have
• Illustrations of wide body freighters such V359, V342, V328

```html
<!DOCTYPE html>
<html lang="en">
<head>
<meta charset="utf-8">
<title>Calder Aviation</title>
<link rel="stylesheet" href="https://fonts.googleapis.com/css2?family=Josefin+Sans:wght@400;600;700&family=Lato:wght@400;700&display=swap">
<style>
:root{
  --navy:#0f1a4d;
  --navy-deep:#0b1440;
  --steel:#a9b8c8;
  --ink:#1a1a2e;
  --text:#444a55;
  --white:#ffffff;
  --pale:#f2f4f8;
}
*{box-sizing:border-box;margin:0;padding:0}
html,body{width:1200px;height:3974px;overflow:hidden}
body{position:relative;background:var(--white);font-family:"Lato",sans-serif;color:var(--text)}
.abs{position:absolute}
.display{font-family:"Josefin Sans",sans-serif;font-weight:400}
a{color:inherit;text-decoration:none}

/* hero */
.hero{position:absolute;left:0;top:0;width:1200px;height:700px;background:linear-gradient(180deg,#17245f 0%,#243574 45%,#5a6c9c 75%,#36477f 100%)}
.brand{position:absolute;color:var(--white);text-align:center;font-family:"Josefin Sans",sans-serif;font-weight:400;line-height:1}
.brand .name{font-size:24px;letter-spacing:1px}
.brand .sub{font-size:11px;letter-spacing:10px;margin-top:6px}
.nav{position:absolute;top:26px;left:351px;color:var(--white);font-size:15px;font-family:"Josefin Sans",sans-serif}
.nav a{position:absolute;white-space:nowrap}
.hero-title{position:absolute;left:110px;top:200px;font-size:44px;line-height:50px;color:var(--white);letter-spacing:1px;font-family:"Josefin Sans",sans-serif;font-weight:400;white-space:nowrap}
.hero-lead{position:absolute;left:112px;top:268px;width:580px;font-size:16px;line-height:26px;color:var(--white);font-family:"Josefin Sans",sans-serif}
.btn{position:absolute;display:flex;height:50px;width:190px;border:2px solid var(--white)}
.btn .label{flex:1;display:flex;align-items:center;padding-left:14px;font-size:20px;font-weight:600;font-family:"Josefin Sans",sans-serif}
.btn .arrow{width:48px;background:var(--steel);display:flex;align-items:center;justify-content:center}
.btn-light .label{background:var(--white);color:var(--navy)}
.btn-dark{border-color:var(--navy)}
.btn-dark .label{background:var(--navy);color:var(--white)}
.follow{position:absolute;left:110px;top:508px;display:flex;align-items:center;gap:12px;color:var(--white);font-size:14px;letter-spacing:4px}
.follow .rule{width:74px;height:1px;background:var(--white)}
.follow .dots{display:flex;gap:12px;margin-left:4px}
.follow .dots span{width:20px;height:20px;border-radius:50%;background:var(--white)}
.contact-line{position:absolute;top:506px;color:var(--white);font-size:14px;display:flex;align-items:center;gap:8px}

/* section labels */
.tag{position:absolute;display:flex;align-items:center;gap:12px;font-size:14px;font-weight:700;color:var(--ink)}
.tag .mark{width:32px;height:28px;background:var(--navy);position:relative}
.tag .mark::after{content:"";position:absolute;left:10px;top:9px;width:24px;height:2px;background:var(--steel);transform:rotate(-25deg)}
h2.title{position:absolute;font-size:32px;line-height:42px;color:var(--ink)}
.para{position:absolute;font-size:14px}

.photo{position:absolute;border-radius:6px}

/* services */
.band{position:absolute;left:0;width:1200px;background:linear-gradient(160deg,#0c1645 0%,#17225a 60%,#0d1746 100%)}
.services{top:1326px;height:561px;clip-path:polygon(110px 0,1200px 0,1200px 494px,1088px 561px,0 561px,0 62px)}
.card{position:absolute;top:1432px;width:244px;height:328px;background:var(--white);text-align:center}
.card .icon{width:84px;height:84px;border-radius:50%;margin:26px auto 0;display:flex;align-items:center;justify-content:center;box-shadow:0 4px 14px rgba(15,26,77,.15);background:var(--white)}
.card .icon.solid{background:var(--navy)}
.card h3{font-family:"Josefin Sans",sans-serif;font-weight:400;font-size:20px;color:var(--ink);margin-top:20px;white-space:nowrap}
.card p{font-size:14px;line-height:26px;color:var(--text);padding:0 20px;margin-top:10px}
.card .go{position:absolute;right:0;bottom:0;width:40px;height:30px;background:#7a8290;display:flex;align-items:center;justify-content:center}

/* sale */
.checks{position:absolute;left:111px;top:2208px;display:grid;grid-template-columns:214px 200px;row-gap:17px;font-size:14px;color:var(--ink)}
.checks li{list-style:none;display:flex;align-items:center;gap:10px;height:22px}

/* contact */
.contact{top:2505px;height:665px;clip-path:polygon(110px 0,1200px 0,1200px 595px,1095px 665px,0 665px,0 75px)}
.field-label{position:absolute;font-size:14px;color:var(--white)}
.field{position:absolute;background:var(--white);border-radius:4px;font-size:11px;color:#7a8290;padding:22px 22px}
.submit{position:absolute;left:518px;top:3046px;width:190px;height:60px;background:var(--steel);color:var(--navy);font-weight:700;font-size:20px;display:flex;align-items:center;justify-content:center;font-family:"Josefin Sans",sans-serif}

/* partners */
.partner{position:absolute;top:3280px;background:#4a4a4a}

/* footer */
.footer{position:absolute;left:0;top:3540px;width:1200px;height:434px;background:var(--navy)}
.col-title{position:absolute;font-family:"Josefin Sans",sans-serif;font-weight:400;font-size:20px;color:var(--white)}
.links{position:absolute;list-style:none;font-size:15px;color:var(--white)}
.links li{height:37px}
.social li{display:flex;align-items:center;gap:14px;height:43px}
.social i{width:20px;height:20px;border-radius:50%;background:#4f6bd6;display:block}
</style>
</head>
<body>

<header class="hero" role="img" aria-label="Passenger jet flying above the clouds at dusk"></header>
<svg class="abs" style="left:0;top:580px" width="1200" height="120" viewBox="0 0 1200 120" aria-hidden="true">
  <path d="M0 14 L600 84 L1200 14 L1200 40 L600 110 L0 40Z" fill="#a9b8c8"/>
  <path d="M0 40 L600 110 L1200 40 L1200 120 L0 120Z" fill="#ffffff"/>
  <path d="M600 60 L604 80 L620 84 L604 88 L600 104 L596 88 L580 84 L596 80Z" fill="#ffffff"/>
</svg>

<div class="brand" style="left:110px;top:14px"><div class="name">CALDER</div><div class="sub">AVIATION</div></div>
<nav class="nav">
  <a style="left:0">Home</a><a style="left:81px">About us</a><a style="left:185px">Services</a><a style="left:285px">Sale/Lease</a><a style="left:406px">Aircraft Management</a><a style="left:607px">Contact us</a>
  <svg style="position:absolute;left:719px;top:2px" width="14" height="14" viewBox="0 0 14 14"><circle cx="6" cy="6" r="4.5" fill="none" stroke="#fff" stroke-width="1.5"/><path d="M9.5 9.5L13 13" stroke="#fff" stroke-width="1.5"/></svg>
</nav>
<h1 class="hero-title">Welcome To CALDER AVIATION</h1>
<p class="hero-lead">We facilitate the arrangement of full charters to airlines and logistics companies. Certain territory restrictions may apply.</p>
<a class="btn btn-light" style="left:111px;top:344px"><span class="label">Get Started</span><span class="arrow"><svg width="28" height="12" viewBox="0 0 28 12"><path d="M0 6H26M21 1L26 6L21 11" fill="none" stroke="#0f1a4d" stroke-width="2"/></svg></span></a>
<div class="follow">Follow us <span class="rule"></span><span class="dots"><span></span><span></span><span></span><span></span></span></div>
<div class="contact-line" style="left:717px"><svg width="14" height="14" viewBox="0 0 14 14"><path d="M3 1L5.5 4L4 6C5 8 6 9 8 10L10 8.5L13 11L11 13C6 13 1 8 1 3Z" fill="#fff"/></svg>123-456(7890)</div>
<div class="contact-line" style="left:865px"><svg width="14" height="10" viewBox="0 0 14 10"><rect width="14" height="10" fill="#fff"/><path d="M0 0L7 6L14 0" fill="none" stroke="#243574" stroke-width="1.2"/></svg>CalderAviation@skymail.net</div>

<!-- about -->
<div class="photo" style="left:110px;top:772px;width:226px;height:460px;background:linear-gradient(180deg,#6f86c4 0%,#c9a0b6 45%,#d38a6a 70%,#3e3f66 100%)" role="img" aria-label="Front view of an airliner in flight against a colourful sunset sky"></div>
<div class="photo" style="left:352px;top:772px;width:274px;height:215px;background:linear-gradient(180deg,#2b4a7a 0%,#c67a3a 55%,#2a2f3a 100%)" role="img" aria-label="Airport apron with parked aircraft at dusk"></div>
<div class="photo" style="left:351px;top:1002px;width:276px;height:230px;background:linear-gradient(180deg,#e7a22a 0%,#f0b43c 55%,#3a3528 100%)" role="img" aria-label="Airliner taxiing on a runway under a golden sky"></div>
<div class="tag" style="left:689px;top:767px"><span class="mark"></span>ABOUT US</div>
<h2 class="title display" style="left:688px;top:806px">Founded in 2011, Calder<br>Aviation's management</h2>
<p class="para" style="left:689px;top:906px;width:396px;line-height:29px">Many years of experience in Aviation, a strong background in scheduled airlines with emphasis in all cargo operations, freight forwarding supply chain and freight logistics, as well as ACMI and CMI operations.Calder’s focuses in facilitating wet and dry lease operations, charter and ACMI programs consultancy, aircraft sales, leasing and procurement, aviation consultancy.</p>
<a class="btn btn-dark" style="left:689px;top:1141px"><span class="label">Read More</span><span class="arrow"><svg width="28" height="12" viewBox="0 0 28 12"><path d="M0 6H26M21 1L26 6L21 11" fill="none" stroke="#0f1a4d" stroke-width="2"/></svg></span></a>

<!-- services -->
<section class="band services" role="img" aria-label="Dark navy backdrop with a faint parked airliner"></section>
<div class="tag" style="left:111px;top:1423px;color:#fff"><span class="mark" style="background:var(--steel)"></span>SERVICES</div>
<h2 class="title display" style="left:111px;top:1482px;color:#fff">Our Services</h2>
<p class="para" style="left:111px;top:1541px;width:236px;line-height:34px;color:#fff">Calder buys, sells, leases and facilitates aircraft trading while specializes in structured aircraft investment projects.</p>
<a class="btn btn-light" style="left:112px;top:1708px"><span class="label">Read More</span><span class="arrow"><svg width="28" height="12" viewBox="0 0 28 12"><path d="M0 6H26M21 1L26 6L21 11" fill="none" stroke="#0f1a4d" stroke-width="2"/></svg></span></a>

<article class="card" style="left:387px">
  <div class="icon solid"><svg width="40" height="40" viewBox="0 0 40 40"><path d="M6 22L34 14M14 20L10 30M24 17L30 8" stroke="#fff" stroke-width="2" fill="none"/><circle cx="20" cy="32" r="3" fill="none" stroke="#fff" stroke-width="1.5"/></svg></div>
  <h3>Aircraft Finance</h3>
  <p>We provide aircraft owners Aircraft Management services, where we manage the technical side of the aircraft or the asset.</p>
  <span class="go"><svg width="22" height="10" viewBox="0 0 22 10"><path d="M0 5H20M16 1L20 5L16 9" fill="none" stroke="#fff" stroke-width="1.5"/></svg></span>
</article>
<article class="card" style="left:655px">
  <div class="icon"><svg width="40" height="40" viewBox="0 0 40 40"><rect x="6" y="8" width="28" height="22" fill="none" stroke="#0f1a4d" stroke-width="1.5"/><path d="M11 26V20M16 26V16M21 26V18M26 26V13" stroke="#0f1a4d" stroke-width="2"/><path d="M14 34H26" stroke="#0f1a4d" stroke-width="1.5"/></svg></div>
  <h3>Trading</h3>
  <p>We provide aircraft owners Aircraft Management services, where we manage the technical side of the aircraft or the asset.</p>
  <span class="go"><svg width="22" height="10" viewBox="0 0 22 10"><path d="M0 5H20M16 1L20 5L16 9" fill="none" stroke="#fff" stroke-width="1.5"/></svg></span>
</article>
<article class="card" style="left:924px">
  <div class="icon"><svg width="40" height="40" viewBox="0 0 40 40"><path d="M6 11H34M6 20H34M6 29H34" stroke="#0f1a4d" stroke-width="1.5"/><circle cx="24" cy="11" r="3" fill="#fff" stroke="#0f1a4d" stroke-width="1.5"/><circle cx="14" cy="20" r="3" fill="#fff" stroke="#0f1a4d" stroke-width="1.5"/><circle cx="22" cy="29" r="3" fill="#fff" stroke="#0f1a4d" stroke-width="1.5"/></svg></div>
  <h3>Procurement &amp; Leasing</h3>
  <p>Leaseback arrangements are usually employed because they confer financing, accounting or taxation benefits.</p>
  <span class="go"><svg width="22" height="10" viewBox="0 0 22 10"><path d="M0 5H20M16 1L20 5L16 9" fill="none" stroke="#fff" stroke-width="1.5"/></svg></span>
</article>

<!-- sale / lease -->
<div class="tag" style="left:111px;top:1963px"><span class="mark"></span>SALE/LEASEBACK</div>
<h2 class="title display" style="left:113px;top:2025px">Aircraft Available for Sale/Lease</h2>
<p class="para" style="left:111px;top:2086px;width:470px;line-height:26px;color:var(--ink)">Calder team is a hands-on reliable alternative that works toward achieving your aircraft and aviation objectives by meeting your requirements and timeframe throughout professional and personalized service.</p>
<ul class="checks">
  <li><svg width="20" height="20" viewBox="0 0 20 20"><circle cx="10" cy="10" r="10" fill="#0f1a4d"/><path d="M5.5 10L8.5 13L14.5 7" stroke="#fff" stroke-width="2" fill="none"/></svg>Sale/Leaseback</li>
  <li><svg width="20" height="20" viewBox="0 0 20 20"><circle cx="10" cy="10" r="10" fill="#0f1a4d"/><path d="M5.5 10L8.5 13L14.5 7" stroke="#fff" stroke-width="2" fill="none"/></svg>Dry Lease</li>
  <li><svg width="20" height="20" viewBox="0 0 20 20"><circle cx="10" cy="10" r="10" fill="#0f1a4d"/><path d="M5.5 10L8.5 13L14.5 7" stroke="#fff" stroke-width="2" fill="none"/></svg>Aviation Consultancy</li>
  <li><svg width="20" height="20" viewBox="0 0 20 20"><circle cx="10" cy="10" r="10" fill="#0f1a4d"/><path d="M5.5 10L8.5 13L14.5 7" stroke="#fff" stroke-width="2" fill="none"/></svg>Wet lease</li>
  <li><svg width="20" height="20" viewBox="0 0 20 20"><circle cx="10" cy="10" r="10" fill="#0f1a4d"/><path d="M5.5 10L8.5 13L14.5 7" stroke="#fff" stroke-width="2" fill="none"/></svg>Aircraft Management</li>
  <li><svg width="20" height="20" viewBox="0 0 20 20"><circle cx="10" cy="10" r="10" fill="#0f1a4d"/><path d="M5.5 10L8.5 13L14.5 7" stroke="#fff" stroke-width="2" fill="none"/></svg>Worldwide Charters</li>
</ul>
<a class="btn btn-dark" style="left:111px;top:2380px"><span class="label">View More</span><span class="arrow"><svg width="28" height="12" viewBox="0 0 28 12"><path d="M0 6H26M21 1L26 6L21 11" fill="none" stroke="#0f1a4d" stroke-width="2"/></svg></span></a>
<div class="abs" style="left:690px;top:1963px;width:400px;height:305px;background:linear-gradient(135deg,#5c6470 0%,#8a8f96 40%,#e6c64a 60%,#b9bec5 100%)" role="img" aria-label="Wide-body freighter parked at a cargo stand, seen from above"></div>
<div class="abs" style="left:628px;top:2148px;width:270px;height:202px;background:#fff;padding:6px">
  <div style="width:100%;height:100%;background:linear-gradient(180deg,#6f8fc9 0%,#a9bfe0 50%,#4a6a2c 80%,#34501e 100%)" role="img" aria-label="Wide-body freighter on the taxiway under a blue sky"></div>
</div>

<!-- contact -->
<section class="band contact" role="img" aria-label="Dark navy backdrop with a faint aircraft silhouette"></section>
<h2 class="title display" style="left:0;width:1180px;text-align:center;top:2566px;color:#fff">Get In Touch</h2>
<label class="field-label" style="left:110px;top:2663px">Your Name</label>
<div class="field" style="left:110px;top:2690px;width:474px;height:60px">Alex Rowan</div>
<label class="field-label" style="left:616px;top:2663px">Address</label>
<div class="field" style="left:616px;top:2690px;width:474px;height:60px">12 Harbor Lane, us</div>
<label class="field-label" style="left:110px;top:2775px">Email Address</label>
<div class="field" style="left:110px;top:2802px;width:474px;height:60px">alex.rowan@mailbox.net</div>
<label class="field-label" style="left:616px;top:2775px">Message</label>
<div class="field" style="left:616px;top:2802px;width:474px;height:176px;padding-top:28px">Type message here.......</div>
<label class="field-label" style="left:110px;top:2890px">Phone No</label>
<div class="field" style="left:110px;top:2918px;width:474px;height:60px">123-456-7890</div>
<div class="submit">SUBMIT</div>

<!-- partners -->
<div class="partner" style="left:124px;top:3296px;width:124px;height:36px"></div>
<div class="partner" style="left:358px;width:86px;height:80px;border-radius:8px 8px 43px 43px"></div>
<div class="partner" style="left:552px;top:3294px;width:122px;height:44px;border-radius:50%"></div>
<div class="partner" style="left:772px;width:104px;height:90px;border-radius:50%"></div>
<div class="partner" style="left:980px;top:3302px;width:92px;height:40px;border-radius:20px"></div>

<!-- footer -->
<svg class="abs" style="left:0;top:3440px" width="1200" height="101" viewBox="0 0 1200 101" aria-hidden="true">
  <path d="M0 80 L600 15 L1200 80 L1200 101 L0 101Z" fill="#a9b8c8"/>
  <path d="M0 96 L600 40 L1200 96 L1200 101 L0 101Z" fill="#0f1a4d"/>
  <path d="M602 0 L606 18 L622 22 L606 26 L602 44 L598 26 L582 22 L598 18Z" fill="#0f1a4d"/>
</svg>
<footer class="footer"></footer>
<div class="brand" style="left:125px;top:3612px"><div class="name" style="font-size:30px">CALDER</div><div class="sub" style="font-size:13px;letter-spacing:14px">AVIATION</div></div>
<p class="para" style="left:112px;top:3690px;width:370px;line-height:31px;color:#fff">Calder’s focuses in facilitating wet and dry lease operations, charter and ACMI programs consultancy, aircraft sales, leasing and procurement, aviation &amp; aircraft management.</p>
<h4 class="col-title" style="left:555px;top:3598px">Quick Links</h4>
<ul class="links" style="left:555px;top:3647px"><li>Home</li><li>About us</li><li>Our Services</li><li>Aircraft Available</li><li>Contact us</li></ul>
<h4 class="col-title" style="left:769px;top:3596px">Help Links</h4>
<ul class="links" style="left:769px;top:3645px"><li>FAQ</li><li>Blog</li><li>Support Center</li><li>Privacy Policy</li><li>Conditions</li></ul>
<h4 class="col-title" style="left:977px;top:3596px">Follow us</h4>
<ul class="links social" style="left:978px;top:3634px"><li><i></i>Friendloop</li><li><i style="background:#d14b8f"></i>Snapgrid</li><li><i style="background:#3aa0e8"></i>Chirpline</li></ul>
<div class="abs" style="left:113px;top:3872px;width:972px;height:1px;background:#6a7499"></div>
<p class="abs" style="left:0;width:1200px;top:3909px;text-align:center;font-size:15px;color:#fff">Copyrights@2021.All Rights Reserved</p>

</body>
</html>
```